Ridgeline Journeys business card

please see website
www.ridgelinejourneys.comau

info needed on card
Curtis Halvey
Ph
email
Adventure Riding GPS trails

please use my logo and colours off my site

Curtis Halvey
curtis@ridgelinejourneys.com

```html
<!DOCTYPE html>
<html lang="en">
<head>
<meta charset="utf-8">
<title>Ridgeline Journeys – Business Card</title>
<link rel="stylesheet" href="https://fonts.googleapis.com/css2?family=Open+Sans:ital,wght@0,400;0,600;0,700;1,700&display=swap">
<style>
  :root {
    --page-bg: #d8d3cb;
    --card-bg: #eeece8;
    --panel-dark: #1c1c1c;
    --panel-dark-edge: #2e2e2e;
    --accent-yellow: #e6c334;
    --accent-gold: #d9a928;
    --text-light: #f2f2f2;
    --brand-ink: #262626;
  }
  * { margin: 0; padding: 0; box-sizing: border-box; }
  html, body {
    width: 1200px;
    height: 969px;
    overflow: hidden;
    background: var(--page-bg);
    font-family: "Open Sans", Arial, sans-serif;
  }
  .business-card {
    position: absolute;
    left: 100px;
    top: 200px;
    width: 1000px;
    height: 570px;
    background: var(--card-bg);
    overflow: hidden;
    box-shadow: 0 10px 30px rgba(0,0,0,0.18);
  }
  .contact-panel {
    position: absolute;
    left: -110px;
    top: 212px;
    width: 620px;
    height: 620px;
    border-radius: 50%;
    background: radial-gradient(circle at 50% 35%, var(--panel-dark-edge), var(--panel-dark) 70%);
  }
  .brand {
    position: absolute;
    left: 510px;
    top: 84px;
    display: flex;
    align-items: center;
    gap: 26px;
  }
  .brand-dot {
    width: 86px;
    height: 86px;
    border-radius: 50%;
    background: var(--accent-yellow);
  }
  .brand-name {
    font-weight: 700;
    font-size: 44px;
    line-height: 1.0;
    color: var(--brand-ink);
    text-transform: uppercase;
    letter-spacing: 0.5px;
  }
  .brand-name span { display: block; }
  .contact-details {
    position: absolute;
    left: 46px;
    top: 306px;
    color: var(--text-light);
  }
  .person-name {
    font-size: 33px;
    font-weight: 600;
    color: var(--accent-yellow);
    margin-bottom: 18px;
  }
  .contact-line {
    display: flex;
    align-items: center;
    gap: 14px;
    font-size: 23px;
    height: 40px;
  }
  .contact-line svg { width: 24px; height: 24px; flex: none; }
  .tagline {
    margin-top: 16px;
    font-size: 24px;
    font-weight: 700;
    font-style: italic;
    color: var(--accent-gold);
    letter-spacing: 0.5px;
  }
</style>
</head>
<body>
  <div class="business-card">
    <div class="contact-panel"></div>

    <div class="brand">
      <div class="brand-dot"></div>
      <div class="brand-name"><span>Ridgeline</span><span>Journeys</span></div>
    </div>

    <div class="contact-details">
      <div class="person-name">Curtis Halvey</div>

      <div class="contact-line">
        <svg viewBox="0 0 24 24" aria-hidden="true">
          <path fill="var(--accent-yellow)" d="M6.6 10.8a15.1 15.1 0 0 0 6.6 6.6l2.2-2.2a1 1 0 0 1 1-.25 11.4 11.4 0 0 0 3.6.57 1 1 0 0 1 1 1V20a1 1 0 0 1-1 1A17 17 0 0 1 3 4a1 1 0 0 1 1-1h3.5a1 1 0 0 1 1 1c0 1.25.2 2.45.57 3.57a1 1 0 0 1-.25 1z"/>
        </svg>
        <span>614 205 7391</span>
      </div>

      <div class="contact-line">
        <svg viewBox="0 0 24 24" aria-hidden="true">
          <rect x="2" y="5" width="20" height="14" rx="1.5" fill="var(--accent-yellow)"/>
          <path d="M3 6.5l9 6.5 9-6.5" fill="none" stroke="var(--panel-dark)" stroke-width="1.8"/>
        </svg>
        <span>curtis@ridgelinejourneys.com</span>
      </div>

      <div class="contact-line">
        <svg viewBox="0 0 24 24" aria-hidden="true">
          <circle cx="12" cy="12" r="10" fill="var(--accent-yellow)"/>
          <path d="M2 12h20M12 2c3 3 3 17 0 20M12 2c-3 3-3 17 0 20" fill="none" stroke="var(--panel-dark)" stroke-width="1.4"/>
        </svg>
        <span>www.ridgelinejourneys.com.au</span>
      </div>

      <div class="tagline">Adventure Riding GPS trails</div>
    </div>
  </div>
</body>
</html>
```